Business Card Design

I need a business card for my tutoring service. Key elements on front are its contact details and visual appeal with these three points: All aspects of literacy and numeracy, 'Steady Steps Learning Grant' provider and Prep-readiness sessions
Updates

contact me by email on ranefol7@quintmail.example as I'm having issues with other address at times. Thanks

:) 

Target Market(s)

People with children

Industry/Entity Type

Tutoring

Contact Information for Business Card

Dora Pilcher Educational Consultant
17 Tasselby Close
Wendrabah 4812
0471 386 912

Requirements
Nice to have
• Something related to education. On the back of the card, my business name and phone number again, along with: spelling, reading, writing, comprehension, oral language, listening skills

```html
<!DOCTYPE html>
<html lang="en">
<head>
<meta charset="utf-8">
<title>Dora Pilcher's Tutoring Service – Business Card</title>
<link href="https://fonts.googleapis.com/css2?family=Oswald:wght@400;500;600&display=swap" rel="stylesheet">
<style>
  :root {
    --sky: #8fd1ee;
    --rose: #ef6b7b;
    --slate: #6b6864;
    --cream: #fdfbe8;
    --stage: #eceae4;
    --white: #ffffff;
  }
  * { box-sizing: border-box; margin: 0; padding: 0; }
  html, body { width: 1200px; height: 800px; overflow: hidden; }
  body {
    background: var(--stage);
    font-family: "Oswald", "Arial Narrow", sans-serif;
    text-transform: uppercase;
    position: relative;
  }
  .card {
    position: absolute;
    top: 245px;
    width: 540px;
    height: 310px;
    background: var(--cream);
    overflow: hidden;
    box-shadow: 0 6px 18px rgba(0,0,0,.15);
  }
  .card--front { left: 50px; }
  .card--back { left: 610px; }
  .card__wave { position: absolute; inset: 0; width: 100%; height: 100%; }
  .card__wave path { fill: var(--sky); }

  /* Front */
  .identity { position: absolute; left: 36px; top: 34px; color: var(--white); }
  .identity__rule { width: 70px; height: 4px; background: var(--rose); margin-bottom: 6px; }
  .identity__name { font-size: 30px; font-weight: 500; letter-spacing: .5px; line-height: 1.1; }
  .identity__role { font-size: 15px; font-weight: 400; letter-spacing: .5px; }
  .contact { position: absolute; left: 36px; top: 146px; display: flex; gap: 14px; color: var(--white); }
  .contact__bar { width: 20px; height: 78px; background: var(--rose); }
  .contact__lines { font-size: 15px; line-height: 1.45; padding-top: 4px; }
  .offer { position: absolute; left: 300px; top: 168px; }
  .offer__title { font-size: 30px; font-weight: 500; line-height: 1; margin-bottom: 8px; white-space: nowrap; }
  .offer__title .pink { color: var(--rose); }
  .offer__title .blue { color: var(--sky); }
  .offer__list { list-style: none; color: var(--slate); font-size: 13px; line-height: 1.35; }

  /* Back */
  .brand { position: absolute; left: 170px; top: 92px; text-align: left; }
  .brand__name { font-size: 50px; font-weight: 500; line-height: 1; letter-spacing: 1px; white-space: nowrap; }
  .brand__name .blue { color: var(--sky); }
  .brand__name .pink { color: var(--rose); }
  .brand__service { font-size: 30px; font-weight: 400; color: var(--slate); line-height: 1.15; margin-left: 48px; }
  .brand__rules { display: flex; margin: 8px 0 0 48px; }
  .brand__rules span { height: 4px; width: 90px; }
  .brand__rules .pink { background: var(--rose); }
  .brand__rules .blue { background: var(--sky); }
  .skills { position: absolute; left: 40px; right: 24px; top: 240px; text-align: center; color: var(--rose); font-size: 12.5px; letter-spacing: .3px; }
</style>
</head>
<body>
  <section class="card card--front" aria-label="Card front">
    <svg class="card__wave" viewBox="0 0 540 310" preserveAspectRatio="none" aria-hidden="true">
      <path d="M0 0 H360 C330 40 250 70 262 140 C272 200 248 260 236 310 H0 Z"/>
    </svg>
    <div class="identity">
      <div class="identity__rule"></div>
      <div class="identity__name">Dora Pilcher</div>
      <div class="identity__role">Educational Consultant</div>
    </div>
    <div class="contact">
      <div class="contact__bar"></div>
      <div class="contact__lines">
        <div>0471 386 912</div>
        <div>17 Tasselby Close</div>
        <div>Wendrabah 4812</div>
      </div>
    </div>
    <div class="offer">
      <div class="offer__title"><span class="pink">Tutoring</span> <span class="blue">Service</span></div>
      <ul class="offer__list">
        <li>All aspects of literacy and numeracy</li>
        <li>Steady Steps Learning Grant</li>
        <li>Prep-readiness sessions</li>
      </ul>
    </div>
  </section>

  <section class="card card--back" aria-label="Card back">
    <svg class="card__wave" viewBox="0 0 540 310" preserveAspectRatio="none" aria-hidden="true">
      <path d="M0 0 H230 C180 30 150 70 168 130 C186 190 120 250 0 290 Z"/>
    </svg>
    <div class="brand">
      <div class="brand__name"><span class="blue">Dora</span> <span class="pink">Pilcher's</span></div>
      <div class="brand__service">Tutoring Service</div>
      <div class="brand__rules"><span class="pink"></span><span class="blue"></span></div>
    </div>
    <p class="skills">Spelling, reading, writing, comprehension, oral language, listening skills</p>
  </section>
</body>
</html>
```